Kestrelbrook Student Accomodation needs a business card design

Hi Guys,

We are a Student Accommodation company in Australia. We already have a logo which I will submit.

I will require the design of the business cards from you.

I am after something that looks clean, modern and that people feel interested and actually want to contact us.

We would like to see designs that are innovative.

On the business cards I will require to have:

Employee Name
Position
Phone number
Email
Facebook page

I hope you can help me with this project guys as I have heard really good things from you.

```html
<!DOCTYPE html>
<html lang="en">
<head>
<meta charset="utf-8">
<title>Kestrelbrook Student Accomodation – Business Card</title>
<link rel="stylesheet" href="https://fonts.googleapis.com/css2?family=Open+Sans:wght@400;700&display=swap">
<style>
  :root {
    --green: #0a8f45;
    --yellow: #fdc12f;
    --white: #ffffff;
    --ink: #1f2a24;
    --backdrop: #e9e6e1;
    --edge: #d6d2cb;
  }
  * { box-sizing: border-box; margin: 0; padding: 0; }
  html, body { width: 1200px; height: 765px; overflow: hidden; }
  body {
    background: var(--backdrop);
    font-family: "Open Sans", Arial, sans-serif;
    position: relative;
  }
  .card {
    position: absolute;
    width: 597px;
    height: 341px;
    background: var(--white);
    border: 1px solid var(--edge);
    overflow: hidden;
  }
  .card--front { left: 102px; top: 52px; z-index: 2; }
  .card--back  { left: 519px; top: 351px; z-index: 1; }

  .brand {
    position: absolute;
    left: 0; right: 0;
    display: flex;
    align-items: center;
    justify-content: center;
    gap: 12px;
  }
  .brand__mark { background: var(--yellow); flex: none; }
  .brand__name {
    color: var(--green);
    font-weight: 700;
    line-height: 1.1;
    text-transform: uppercase;
  }
  .card--front .brand { top: 58px; }
  .card--front .brand__mark { width: 54px; height: 54px; }
  .card--front .brand__name { font-size: 22px; }
  .card--back .brand { top: 130px; }
  .card--back .brand__mark { width: 70px; height: 70px; }
  .card--back .brand__name { font-size: 26px; }

  .rule {
    position: absolute; left: 0; right: 0;
    top: 187px; height: 4px;
    background: var(--green);
  }
  .contact-band {
    position: absolute; left: 0; right: 0;
    top: 191px; height: 85px;
    background: var(--yellow);
    display: flex; flex-direction: column;
    align-items: center; justify-content: center;
    gap: 5px;
  }
  .contact {
    display: flex; align-items: center; gap: 7px;
    font-size: 15px; color: var(--ink);
  }
  .contact__icon { width: 13px; height: 13px; flex: none; }
  .name-band {
    position: absolute; left: 0; right: 0;
    top: 276px; height: 60px;
    background: var(--green);
    display: flex; align-items: center; justify-content: center;
    color: var(--white);
  }
  .name-band__name { font-weight: 700; font-size: 19px; letter-spacing: 0.2px; }
  .name-band__role { font-size: 16px; margin-left: 6px; }
  .base-rule {
    position: absolute; left: 0; right: 0;
    top: 336px; height: 5px;
    background: var(--yellow);
  }
</style>
</head>
<body>
  <section class="card card--front" aria-label="Business card front">
    <div class="brand">
      <span class="brand__mark"></span>
      <span class="brand__name">Kestrelbrook<br>Student Accomodation</span>
    </div>
    <div class="rule"></div>
    <div class="contact-band">
      <p class="contact">
        <svg class="contact__icon" viewBox="0 0 24 24" aria-hidden="true"><path fill="var(--green)" d="M6.6 10.8a15.1 15.1 0 0 0 6.6 6.6l2.2-2.2c.3-.3.7-.4 1-.2 1.1.4 2.3.6 3.6.6.6 0 1 .4 1 1V20c0 .6-.4 1-1 1A17 17 0 0 1 3 4c0-.6.4-1 1-1h3.5c.6 0 1 .4 1 1 0 1.3.2 2.5.6 3.6.1.3 0 .7-.2 1z"/></svg>
        123-456-7890
      </p>
      <p class="contact">
        <svg class="contact__icon" viewBox="0 0 24 24" aria-hidden="true"><rect x="2" y="5" width="20" height="14" rx="2" fill="var(--green)"/><path d="M3 6l9 7 9-7" fill="none" stroke="var(--yellow)" stroke-width="1.8"/></svg>
        info@kestrelbrook.com
      </p>
      <p class="contact">
        <svg class="contact__icon" viewBox="0 0 24 24" aria-hidden="true"><rect x="2" y="2" width="20" height="20" rx="2" fill="var(--green)"/></svg>
        /kestrelbrookstudent
      </p>
    </div>
    <div class="name-band">
      <span class="name-band__name">EMPLOYEE NAME,</span>
      <span class="name-band__role">Position</span>
    </div>
    <div class="base-rule"></div>
  </section>

  <section class="card card--back" aria-label="Business card back">
    <div class="brand">
      <span class="brand__mark"></span>
      <span class="brand__name">Kestrelbrook<br>Student Accomodation</span>
    </div>
  </section>
</body>
</html>
```